Homepage for the brisk-find Web Application

At the end of this text, you will find a link to a website that is under construction for a webApp that I intend to launch soon. The contest goal is for you to make redesign the homepage in a nice, fresh, modern Style. Only design, no coding necessary. It needs to have a responsive version for small screens like smart phones. Attached is the text for it, and some images that you may use. You are welcome to find or create additional supporting images. You can use PixTrove.example or similar service to find new images as long as I can purchase the non-exclusive use rights for the images at similar prices. The contest is just for the home page. However, the winner, if I like the work and we can agree on a fair price, could be contracted on a one-on-one basis to do the rest of the site. You are welcome to suggest minor changes like font sizes and minor variations on the Header banner, but that banner is consistent with the user interface of the application therefore should not change too much. The information should flow somewhat continually without much use of side bars or things like that.
https://www.brisk-find.example
Sincerely,
Marco D. Ferral

```html
<!DOCTYPE html>
<html lang="en">
<head>
<meta charset="utf-8">
<title>Brisk-Find — Homepage</title>
<link href="https://fonts.googleapis.com/css2?family=Roboto:wght@300;400;500;700&display=swap" rel="stylesheet">
<style>
:root{
  --blue:#2f7bc4;
  --navy:#0c2c60;
  --ink:#2a2f38;
  --coral:#fa7a55;
  --mint:#9fe2d7;
  --section:#eff5f2;
  --white:#ffffff;
}
*{box-sizing:border-box;margin:0;padding:0}
html,body{width:1200px;height:3361px;overflow:hidden;background:var(--white)}
body{font-family:"Roboto",sans-serif;color:var(--ink);position:relative}
.page{position:absolute;left:125px;top:0;width:951px;height:3361px}
.login-bar{position:absolute;left:0;top:0;width:951px;height:82px;background:var(--blue)}
.field{position:absolute;top:31px;height:21px;width:249px;border-radius:11px;background:var(--mint);
  font-size:12px;letter-spacing:1.5px;color:#3b6a78;padding:3px 0 0 14px}
.field--user{left:158px}
.field--pass{left:420px}
.btn-login{position:absolute;left:711px;top:27px;width:82px;height:29px;border-radius:15px;background:var(--white);
  color:var(--blue);font-weight:700;font-size:12px;letter-spacing:2px;text-align:center;line-height:29px}
.hero{position:absolute;left:0;top:82px;width:951px;height:553px;
  background:linear-gradient(120deg,#e8e4dc 0%,#d9d2c4 30%,#c9b79e 55%,#b58a55 75%,#d9b24a 100%)}
.brand{position:absolute;left:60px;top:22px;display:flex;align-items:center;gap:8px}
.brand-mark{width:44px;height:44px;border-radius:50%;border:3px solid #2d3a44;background:var(--white)}
.brand-name{font-size:32px;font-weight:400;color:var(--coral)}
.nav{position:absolute;left:301px;top:38px;display:flex;gap:18px;font-size:14px;letter-spacing:1.4px;color:var(--navy);font-weight:500}
.hero-title{position:absolute;left:36px;top:170px;width:460px;text-align:center;font-size:39px;font-weight:700;
  letter-spacing:5px;line-height:46px;color:var(--navy)}
.btn{position:absolute;border-radius:30px;background:var(--coral);color:var(--navy);font-weight:700;letter-spacing:2.5px;
  text-align:center;box-shadow:0 6px 10px rgba(0,0,0,.15)}
.btn--about{left:165px;top:356px;width:208px;height:62px;line-height:62px;font-size:22px;box-shadow:none}
.content{position:absolute;left:3px;top:635px;width:948px;height:2641px;background:var(--section)}
.art{position:absolute;left:395px;width:160px;height:185px;border-radius:50%/45% 45% 55% 55%;
  background:radial-gradient(circle at 55% 55%,var(--coral) 0 48%,transparent 49%),
  linear-gradient(160deg,#7fd6dc,#3fb0bf)}
.heading{position:absolute;left:3px;width:948px;text-align:center;font-size:36px;font-weight:500;letter-spacing:5px;
  line-height:41px;color:var(--navy)}
.copy{position:absolute;left:46px;width:864px;font-size:19px;font-weight:300;letter-spacing:3px;line-height:32.6px;color:var(--ink)}
.copy strong{font-weight:700;display:block}
.bullets{list-style:none}
.bullets li{margin-bottom:8px}
.divider{position:absolute;left:395px;width:158px;height:4px;background:var(--navy)}
.btn--more{left:391px;top:2173px;width:167px;height:50px;line-height:50px;font-size:18px}
.btn--pricing{left:172px;top:3075px;width:250px;height:51px;line-height:51px;font-size:18px}
.btn--trial{left:514px;top:3075px;width:265px;height:51px;line-height:51px;font-size:18px}
.footer{position:absolute;left:3px;top:3276px;width:948px;height:85px;background:var(--blue);color:var(--white);
  font-size:14px;font-weight:700;letter-spacing:2px}
.footer span{position:absolute;top:33px}
.footer .f-contact{left:27px}
.footer .f-copy{left:315px}
.footer .f-social{left:776px}
</style>
</head>
<body>
<div class="page">
  <header class="login-bar">
    <div class="field field--user">username</div>
    <div class="field field--pass">password</div>
    <div class="btn-login">LOGIN</div>
  </header>

  <section class="hero" role="img" aria-label="Photo of a hand pulling a document from a hanging file drawer">
    <div class="brand"><span class="brand-mark"></span><span class="brand-name">Brisk-Find</span></div>
    <nav class="nav"><span>About</span><span>Pricing</span><span>Blog</span><span>FAQs</span><span>Support</span><span>Review</span><span>Contact Us</span><span>Free-Trial</span></nav>
    <h1 class="hero-title">Find that<br>document or item<br>instantly.</h1>
    <div class="btn btn--about">about us</div>
  </section>

  <main class="content"></main>

  <div class="art" style="top:724px" role="img" aria-label="Illustration of a person pulling files out of a phone"></div>
  <h2 class="heading" style="top:950px">Keeping track of all your paper<br>documents and other belongings has<br>never been easier.</h2>
  <p class="copy" style="top:1106px">Brisk-find is a system that allows you to quickly search for the location of every item that you store or file. It is an essential tool for keeping track of paper documents. In addition, it is incredibly valuable for storing any other kind of physical items. Giving you the ability to quickly find any item, even years after it has been stored. More importantly, using Brisk-find along with some best practice techniques, could allow you to save considerable space without losing fast accessibility of your items.</p>
  <div class="divider" style="top:1442px"></div>

  <div class="art" style="top:1538px" role="img" aria-label="Illustration of a person carrying a document out of a phone"></div>
  <h2 class="heading" style="top:1752px">Why use a storage management<br>system like Brisk-Find?</h2>
  <div class="copy" style="top:1865px"><strong>Managing paper documents</strong>It is quite common for most people and businesses to receive a variety of such documents that need to be filed. The problem is how to efficiently do it in a way that any of it can easily be found, even in a distant future. We normally put them in folders on file drawers sorted by some criteria. But which criterion is the right standard for all kinds of documents? There is no right criterion for every kind of document.</div>
  <div class="btn btn--more">read more</div>
  <div class="divider" style="top:2323px"></div>

  <div class="art" style="top:2420px" role="img" aria-label="Illustration of a person holding a folder beside a phone"></div>
  <h2 class="heading" style="top:2650px">Why Brisk-Find?</h2>
  <ul class="copy bullets" style="top:2717px">
    <li>• It is extremely easy to use.</li>
    <li>• It is Versatile. Since each catalog can have 1 or many levels of depth &nbsp;&nbsp;(folders and sub-folders). Brisk-find does not force you to use a specific filing or storage methodology.</li>
    <li>• It is really affordable. Checkout our pricing plans.</li>
    <li>• Since it is online, your data is available almost anywhere in the world.</li>
    <li>• Your data always travels encrypted.</li>
  </ul>
  <div class="btn btn--pricing">check our pricing</div>
  <div class="btn btn--trial">start 30 days trial</div>

  <footer class="footer">
    <span class="f-contact">-- contact --</span>
    <span class="f-copy">Copyright © 2016 Harbor Ledger LLC</span>
    <span class="f-social">-- social media --</span>
  </footer>
</div>
</body>
</html>
```